Landing page for gamified shopping site

The target market for this Landing Page are Online sellers/merchants

Our website is www.Quorvex.com

Some background information on our site:
"Ready to make shopping more thrilling? With Quorvex, you can join a world of gamified shopping where players get the chance to win awesome products from their favorite brands - all for free! Compete with other customers in an exciting Dash 'n' Grab game and experience retail like never before. Plus, merchants are invited along too: promote your wares on our site and see what kind of wild success awaits!"

We now need a landing page that will target Online Sellers/Merchants. Please see content for this landing page attached.

This landing page will be comprised of 4 pages:
Home
How it Works
Case Studies
Why Free?
See PDF with content, which also breaks down the content in 4 sections.

The design of this landing page should not only look beautiful but also should be designed in a way that appeals to our target market (online merchants) who want to increase sales by showcasing their products on our website quorvex.com. So this landing page is the "bridge" between online merchants and our website Quorvex.com

The landing page design style should focus on clean and modern aesthetics that effectively communicate the intended message and drive conversions. It should also resemble our brand colors (see Quorvex.com)

If we are asked what look and feel we really, really like, here are two examples:

https://vend.brolimart.net/?ref_=hx_start_main

https://vend.brolimart.net/expand?initialSessionID=482-1173645-9081176&ld=XQSearch#label-enrol

What we like here is the choice of COLORS, FONTS & DESIGN ELEMENTS.

WE WOULD HIGHLY CONSIDER A DESIGN SIMILAR TO THIS WHICH IS CLEAN AND ELEGANT:

This is our logo:
https://files.tenvaro.net/folders/7kTqP2wLm9XzRbV4nHcYd3JfGs8UaE1oN?usp=sharing

This is the Quorvex virtual coin incase you want to incorporate it into the design:
https://files.tenvaro.net/file/d/4pWmXcN8rT2yLqZ_-VbKjHs6GdF3oA9eR/view?usp=sharing

We've also added to the attachments two screenshots that can inspire you for the image for the main banner of the site... showing a happy shopper/winner with products, indicating a fun game, fun shopping and winning products. For our image, we envision a very happy and excited shopper with perhaps the quorvex wheel behind the person and images of high-value products, conveying SHOPPING, GAME and WINNING.

Target Market(s)

Online Sellers/ Merchants

Industry/Entity Type

e-commerce

Number of Pages Required

4 page

Font styles to use
Other font styles liked:
• See fonts in this example: https://vend.brolimart.net/?ref_=hx_start_main

Colors

Designer to choose colors to be used in the design.

Requirements
Must have
• The landing page design style should focus on clean and modern aesthetics that effectively communicate the intended message and drive conversions. It should also resemble our brand colors (see Quorvex.com). We would seriously consider a design like this one which is nice and clean... https://vend.brolimart.net/expand?initialSessionID=482-1173645-9081176&ld=XQSearch#label-enrol
Nice to have
• A site that looks modern and beautiful but at the same time FUN and EXCITING. We really like the choice of COLORS, FONTS and DESIGN ELEMENTS used in this landing page: https://vend.brolimart.net/?ref_=hx_start_main

```html
<!DOCTYPE html>
<html lang="en">
<head>
<meta charset="utf-8">
<title>Quorvex — Level Up Your Online Sales Game</title>
<link href="https://fonts.googleapis.com/css2?family=Poppins:wght@300;400;500;600;700&family=Open+Sans:wght@300;400;600;700&display=swap" rel="stylesheet">
<style>
:root{
  --orange:#ff8a00;
  --orange-deep:#f57c00;
  --ink:#1c1c1c;
  --muted:#8a8a8a;
  --soft:#a9a9a9;
  --page-top:#ececec;
  --page-bottom:#f6f6f6;
  --card:#f7f7f7;
  --white:#ffffff;
  --line:#e2e2e2;
  --placeholder:#d6d3dc;
}
*{box-sizing:border-box;margin:0;padding:0}
html,body{width:1200px;height:2486px;overflow:hidden;background:var(--white)}
body{font-family:"Open Sans",sans-serif;color:var(--ink);position:relative}
.page{position:absolute;left:69px;top:0;width:1027px;height:2404px;transform:scale(1.034);transform-origin:0 0;
  background:linear-gradient(var(--page-top) 0,var(--page-top) 1207px,var(--page-bottom) 1207px);border-top:3px solid var(--orange)}
.abs{position:absolute}
.site-header{position:absolute;left:0;top:0;width:1027px;height:100px;z-index:3}
.heading{font-family:"Poppins",sans-serif;font-weight:400;font-size:31px;line-height:38px;letter-spacing:-.2px;text-transform:uppercase;color:var(--ink)}
.heading b{font-weight:700}
.lead{font-size:11px;line-height:15px;color:var(--muted);font-weight:300}
.btn{position:absolute;display:flex;align-items:center;justify-content:center;border-radius:20px;background:linear-gradient(var(--orange),var(--orange-deep));color:var(--white);font-family:"Poppins",sans-serif;font-weight:600;font-size:11px}
.btn-outline{background:var(--white);border:1px solid var(--orange);color:var(--orange)}
.brand{display:flex;align-items:center;gap:6px;font-family:"Poppins",sans-serif;font-weight:700;font-size:32px;line-height:38px;color:var(--ink);letter-spacing:-.5px}
.brand-dot{width:13px;height:13px;border-radius:50%;background:var(--orange)}
.tagline{font-family:"Poppins",sans-serif;font-size:9px;color:var(--ink);letter-spacing:.3px}
.search{left:304px;top:22px;width:466px;height:34px;border-radius:17px;background:var(--white);font-size:11px;color:#b5b5b5;padding:9px 20px}
.search-icon{position:absolute;right:6px;top:5px;width:24px;height:24px;border-radius:50%;border:1px solid var(--line)}
.signin{left:820px;top:31px;font-family:"Poppins",sans-serif;font-size:12px;color:var(--orange);font-weight:500}
.hero{left:20px;top:71px;width:989px;height:348px;border-radius:10px;background:var(--card);box-shadow:0 2px 6px rgba(0,0,0,.04)}
.nav{top:84px;font-family:"Poppins",sans-serif;font-size:11px;color:#555}
.nav-rule{left:20px;top:109px;width:989px;height:1px;background:var(--line)}
.hero-art{left:642px;top:136px;width:305px;height:266px}
.photo{position:absolute;border-radius:50%}
.steps{left:50px;top:591px;width:927px;height:255px;border-radius:10px;background:var(--card)}
.step{position:absolute;width:200px;text-align:center;top:56px}
.step-title{font-family:"Poppins",sans-serif;font-size:12px;line-height:15px;text-transform:uppercase;margin-top:10px}
.step-title b{font-weight:700}
.step-text{font-size:9.5px;line-height:14px;color:var(--soft);margin-top:8px}
.step-arrow{position:absolute;top:96px;width:30px;height:30px;border-radius:50%;border:1px solid var(--line);background:var(--white)}
.case{left:137px;width:752px;height:241px;background:var(--card);border-radius:6px}
.case-title{font-family:"Poppins",sans-serif;font-size:22px;font-weight:500}
.case-title span{color:var(--orange);font-weight:600}
.case-facts{font-size:11px;line-height:16.5px;color:var(--soft);font-weight:300;width:418px;margin-top:16px}
.case-facts strong{font-family:"Poppins",sans-serif;color:var(--ink);font-weight:500;font-size:12.5px}
.case-facts p{margin-bottom:3px}
.beta{left:85px;top:1856px;width:857px;height:238px;background:linear-gradient(90deg,#fbd8a4,#fde7c6);overflow:hidden}
.footer{left:20px;top:2114px;width:989px;height:265px;background:var(--card);border-radius:6px}
.foot-col h4{font-family:"Poppins",sans-serif;font-weight:400;font-size:12px;color:var(--ink);margin-bottom:5px}
.foot-col li{list-style:none;font-size:9.5px;color:var(--soft);line-height:18px}
.social{position:absolute;top:2337px;width:24px;height:24px;border-radius:50%;background:#e4e4e4}
</style>
</head>
<body>
<main class="page">

  <section class="abs hero">
    <nav>
      <span class="abs nav" style="left:327px;top:13px">• Home</span>
      <span class="abs nav" style="left:398px;top:13px">• How it Works</span>
      <span class="abs nav" style="left:507px;top:13px">• Case Studies</span>
      <span class="abs nav" style="left:614px;top:13px">• Why Free?</span>
      <span class="abs nav" style="left:809px;top:13px"><span style="color:var(--orange)">♥</span>&nbsp; Wishlist</span>
      <span class="abs nav" style="left:904px;top:13px"><span style="color:var(--orange)">■</span>&nbsp; Cart</span>
    </nav>
    <h1 class="abs heading" style="left:68px;top:98px">Level up your online<br><b>Sales game</b> with Quorvex</h1>
    <p class="abs lead" style="left:68px;top:182px;width:450px">Welcome to Quorvex, the ultimate gamified shopping platform where merchants can level up their online sales game. Our platform offers an exciting Dash 'n' Grab game.</p>
    <a class="btn" style="left:67px;top:224px;width:112px;height:30px">Join Now</a>
  </section>
  <div class="nav-rule abs"></div>

  <header class="site-header">
    <div class="abs" style="left:52px;top:38px">
      <div class="brand"><span>Quorvex.com</span><span class="brand-dot"></span></div>
      <div class="tagline" style="margin-top:2px">Spin to win the brands you love — free</div>
    </div>
    <div class="abs search">Search products for you.....<span class="search-icon"></span></div>
    <div class="abs signin">Sign in/</div>
    <a class="btn" style="left:877px;top:22px;width:97px;height:33px">Join Now</a>
  </header>

  <div class="abs hero-art" role="img" aria-label="Excited shopper holding a phone in front of a pink circle, with a prize wheel, sparkles and a shopping bag">
    <div class="photo" style="left:35px;top:40px;width:206px;height:206px;background:radial-gradient(circle at 40% 40%,#ff5fd6,#e83cbc)"></div>
    <div class="photo" style="left:80px;top:0;width:120px;height:250px;border-radius:60px 60px 20px 20px;background:linear-gradient(#6b4a3a,#e9e9e9 45%,#dcdcdc)"></div>
    <div class="photo" style="left:6px;top:8px;width:56px;height:56px;background:var(--placeholder)"></div>
    <div class="abs" style="left:232px;top:186px;width:60px;height:70px;border-radius:8px;background:#8e8ca8"></div>
  </div>

  <section>
    <h2 class="abs heading" style="left:0;width:1027px;top:463px;text-align:center">How <b>Quorvex works</b> -<br>Get ready to Dash 'n' Grab</h2>
    <p class="abs lead" style="left:254px;top:545px;width:520px;text-align:center">Ready to learn how Quorvex works? It's easy! Simply create an account and start playing our Dash 'n' Grab game. Each spin gives you the chance to win awesome products.</p>
    <div class="abs steps">
      <div class="step" style="left:42px">
        <svg width="30" height="30" viewBox="0 0 30 30"><rect x="2" y="2" width="12" height="12" rx="2" fill="#ff8a00"/><rect x="16" y="16" width="12" height="12" rx="2" fill="#ff8a00"/><rect x="16" y="2" width="12" height="12" rx="2" fill="#ffd9a8"/><rect x="2" y="16" width="12" height="12" rx="2" fill="#ffd9a8"/><path d="M5 8l2 2 4-4M19 22l2 2 4-4" stroke="#fff" stroke-width="1.6" fill="none"/></svg>
        <div class="step-title">Select your<br><b>products</b></div>
        <p class="step-text">Choose your favorite products from the available giveaways and add them to your Dash 'n' Grab cart.</p>
      </div>
      <div class="step-arrow" style="left:292px"><svg width="28" height="28" viewBox="0 0 28 28"><path d="M12 9l5 5-5 5" stroke="#999" fill="none"/></svg></div>
      <div class="step" style="left:369px">
        <svg width="30" height="30" viewBox="0 0 30 30"><circle cx="15" cy="15" r="13" fill="#ff8a00"/><path d="M15 15L15 2M15 15L26 22M15 15L4 22" stroke="#fff" stroke-width="2.5"/><circle cx="15" cy="15" r="3" fill="#fff"/></svg>
        <div class="step-title">Spin the<br><b>wheel</b></div>
        <p class="step-text">Once your cart is ready, it's time to spin the wheel! Hold the highest score when the timer hits 0:00 and you're a winner.</p>
      </div>
      <div class="step-arrow" style="left:622px"><svg width="28" height="28" viewBox="0 0 28 28"><path d="M12 9l5 5-5 5" stroke="#999" fill="none"/></svg></div>
      <div class="step" style="left:688px">
        <svg width="30" height="30" viewBox="0 0 30 30"><circle cx="15" cy="15" r="11" fill="none" stroke="#ff8a00" stroke-width="4" stroke-dasharray="5 3"/><circle cx="15" cy="15" r="5" fill="#ff8a00"/></svg>
        <div class="step-title">You win<br><b>prizes</b></div>
        <p class="step-text">Congratulations, all the products in your Dash 'n' Grab cart are yours for free - no strings attached!</p>
      </div>
      <p class="abs" style="left:98px;top:194px;font-size:12px;line-height:14px;color:#333">At Quorvex, it's always free to play and free to win. So why wait?<br>Try your luck today and see what kind of <b>amazing products you could win!</b></p>
      <a class="btn btn-outline" style="left:652px;top:194px;width:102px;height:29px">Join Now</a>
    </div>
  </section>

  <section>
    <h2 class="abs heading" style="left:88px;top:882px">Case studies - the power<br>of gamified <b>shopping contests</b></h2>
    <p class="abs lead" style="left:88px;top:963px">Want to know if gamified shopping contests really work? Take a look at these case studies and be the judge!</p>

    <article class="abs case" style="top:1011px">
      <div class="abs" style="left:30px;top:33px">
        <h3 class="case-title">Case Study #1: <span>MyHexBoards.com</span></h3>
        <div class="case-facts">
          <p><strong>Desired Outcome:</strong>&nbsp; Increase customers and sales revenue</p>
          <p><strong>Contest Duration:</strong>&nbsp; 12 days</p>
          <p><strong>Results:</strong>&nbsp; 1,500 more Friendbook Likes, 400 more Chirper followers, 670 followers on Snapgram, doubled the email subscribers to 1,000, and increased Tumblio followers by 123. All of those activities led to a 4x increase in sales for the contest launch date, which was the best sales day ever for WhiskerWorks!</p>
        </div>
      </div>
      <div class="photo" role="img" aria-label="Hands typing on a laptop showing an online store" style="left:528px;top:30px;width:186px;height:186px;background:radial-gradient(circle,#8a4a3e,#3a2e2a)"></div>
      <div class="photo" role="img" aria-label="Phone showing a shopping app" style="left:469px;top:157px;width:58px;height:58px;background:radial-gradient(circle,#b2525e,#4a3530)"></div>
    </article>

    <article class="abs case" style="top:1274px">
      <div class="photo" role="img" aria-label="Beard care bottles and tins under blue and pink light" style="left:37px;top:25px;width:186px;height:186px;background:radial-gradient(circle at 40% 40%,#a8c4ff,#4c4ee0 60%,#8a3ad0)"></div>
      <div class="photo" role="img" aria-label="Close-up of a grooming product tin" style="left:219px;top:159px;width:58px;height:58px;background:radial-gradient(circle,#ff9ad8,#a67cf0)"></div>
      <div class="abs" style="left:313px;top:33px">
        <h3 class="case-title">Case Study #2: <span>WhiskerWorks.com</span></h3>
        <div class="case-facts">
          <p><strong>Desired Outcome:</strong>&nbsp; Increase customers and sales revenue</p>
          <p><strong>Contest Duration:</strong>&nbsp; 12 days</p>
          <p><strong>Results:</strong>&nbsp; 1,500 more Friendbook Likes, 400 more Chirper followers, 670 followers on Snapgram, doubled the email subscribers to 1,000, and increased Tumblio followers by 123. All of those activities led to a 4x increase in sales for the contest launch date, which was the best sales day ever for WhiskerWorks!</p>
        </div>
      </div>
    </article>

    <article class="abs case" style="top:1536px">
      <div class="abs" style="left:30px;top:33px">
        <h3 class="case-title">Case Study #3: <span>GemAroma.com</span></h3>
        <div class="case-facts">
          <p><strong>Desired Outcome:</strong>&nbsp; Increase customers and sales revenue</p>
          <p><strong>Contest Duration:</strong>&nbsp; 12 days</p>
          <p><strong>Results:</strong>&nbsp; 1,500 more Friendbook Likes, 400 more Chirper followers, 670 followers on Snapgram, doubled the email subscribers to 1,000, and increased Tumblio followers by 123. All of those activities led to a 4x increase in sales for the contest launch date, which was the best sales day ever for WhiskerWorks!</p>
        </div>
      </div>
      <div class="photo" role="img" aria-label="Scented candles in jars with lilac flowers" style="left:529px;top:25px;width:186px;height:186px;background:radial-gradient(circle at 50% 40%,#f6efe8,#e2a57a 55%,#8e6ad0)"></div>
      <div class="photo" role="img" aria-label="Close-up of a candle jar label" style="left:472px;top:152px;width:58px;height:58px;background:radial-gradient(circle,#f1ece6,#c9b9a6)"></div>
    </article>

    <a class="btn" style="left:430px;top:1799px;width:168px;height:31px">Study All the Cases</a>
  </section>

  <section class="abs beta">
    <h2 class="abs heading" style="left:58px;top:42px">Join our beta-<br>launch <b>program today</b></h2>
    <p class="abs lead" style="left:58px;top:128px;width:440px;color:#8a7660">Are you ready to take your online business to the next level? Join Quorvex's beta-launch program today and receive 12 months of free unlimited campaigns, valued at $2,388, plus a free store on our platform.</p>
    <a class="btn" style="left:58px;top:175px;width:113px;height:30px">Join Now</a>
    <div class="abs" role="img" aria-label="Excited man in an orange sweater looking at his phone, in front of an orange circle" style="left:547px;top:13px;width:250px;height:225px;overflow:hidden">
      <div class="photo" style="left:0;top:33px;width:250px;height:250px;background:radial-gradient(circle,#ffb347,#f39a1e)"></div>
      <div class="abs" style="left:65px;top:0;width:120px;height:225px;border-radius:60px 60px 10px 10px;background:linear-gradient(#3a2a22 0,#3a2a22 25%,#c4592a 45%,#a9471f)"></div>
    </div>
  </section>

  <footer class="abs footer">
    <div class="abs" style="left:80px;top:40px">
      <div class="brand" style="font-size:28px;line-height:34px"><span>Quorvex.com</span><span class="brand-dot"></span></div>
      <div class="tagline" style="margin-top:4px">Spin to win the brands you love — free</div>
      <p style="font-family:Poppins,sans-serif;font-weight:600;font-size:10px;margin-top:14px">Got Question? Call us 24/7</p>
      <p style="font-size:10px;color:var(--orange);margin-top:6px">1-800-555-0142</p>
      <p style="font-size:9.5px;line-height:12px;color:var(--soft);margin-top:8px;width:200px">Register now to get updates on promotions, new deals &amp; coupons straight to your inbox.</p>
    </div>
    <div class="abs foot-col" style="left:419px;top:74px"><h4>Company</h4><ul><li>About Us</li><li>Contact Us</li><li>Order History</li></ul></div>
    <div class="abs foot-col" style="left:588px;top:74px"><h4>My Account</h4><ul><li>View Cart</li><li>Sign In</li><li>Wishlist</li></ul></div>
    <div class="abs foot-col" style="left:779px;top:74px"><h4>Customer Service</h4><ul><li>Payment Methods</li><li>Products Returns</li><li>Term and Condition</li></ul></div>
    <div class="abs" style="left:80px;top:210px;width:829px;height:1px;background:var(--line)"></div>
    <span class="abs" style="left:81px;top:228px;font-size:12px;color:var(--muted)">Privacy Policy</span>
    <span class="abs" style="left:0;width:989px;text-align:center;top:228px;font-size:12px;color:var(--muted)">Copyright@Quorvex.com</span>
  </footer>
  <span class="social" style="left:761px"></span>
  <span class="social" style="left:797px"></span>
  <span class="social" style="left:833px"></span>
  <span class="social" style="left:869px"></span>

</main>
</body>
</html>
```